Casa Morellina Togo Menu seperated in categories

new to go menu for italian restaurant with menu descriptions and prices i like the cover first page to have all the restaurant information, the other pages should be separated in the menu categories, and if we can include a map with the location of the restaurant
Casa Morellina
42 Route 83 S
North Myrtle Beach, SC 29582
open 7 days a week 4-10
Happy hour served Daily at the Bar 4-7
www.casamorellina.com
casamorellinadine@maildrop.example

Restaurant

Sans Serif

Must have
• Prices and pictures and restaurant information

```html
<!DOCTYPE html>
<html lang="en">
<head>
<meta charset="utf-8">
<title>Casa Morellina – To Go Menu</title>
<link href="https://fonts.googleapis.com/css2?family=Didact+Gothic&display=swap" rel="stylesheet">
<style>
  :root {
    --tan: #cb8c5e;
    --paper: #f2f3f5;
    --crimson: #b3154a;
    --green: #3b8575;
    --white: #ffffff;
    --ink: #111111;
    --crest: #f7e2a6;
  }
  html, body { margin: 0; padding: 0; overflow: hidden; }
  body { width: 849px; height: 1200px; background: var(--tan); }
  .menu-page { position: relative; width: 849px; height: 1200px; overflow: hidden; }
  .tab-frame { position: absolute; inset: 0; }
  .menu-panel {
    position: absolute; left: 107px; top: 97px; width: 636px; height: 1006px;
    background: var(--paper);
  }
  .crest-name {
    position: absolute; left: 107px; top: 520px; width: 636px;
    text-align: center; margin: 0;
    font-family: "Didact Gothic", sans-serif; font-size: 64px; line-height: 70px;
    color: var(--crest); letter-spacing: 2px;
  }
  .dish {
    position: absolute; left: 121px; width: 608px;
    font-family: "Didact Gothic", sans-serif; color: var(--ink);
    font-size: 16.2px; line-height: 21px;
  }
  .dish-name { margin: 0; font-weight: 400; font-size: 19px; line-height: 21px; color: var(--crimson); }
  .dish-desc { margin: 0; }
  .dish-desc .line { display: block; white-space: nowrap; text-align: justify; text-align-last: justify; }
  .dish-desc .line--last { text-align-last: left; }
  .dish-price { margin: 0; }
  .dish--francaise { top: 118px; }
  .dish--saltimbocca { top: 245px; }
  .dish--margarita { top: 372px; }
  .dish--sorrento { top: 478px; }
  .dish-photo { position: absolute; left: 0; top: 0; }
</style>
</head>
<body>
<div class="menu-page">
  <svg class="tab-frame" width="849" height="1200" viewBox="0 0 849 1200" aria-hidden="true">
    <defs>
      <pattern id="tabs-row" x="107" y="0" width="105.66" height="1200" patternUnits="userSpaceOnUse">
        <rect x="0" y="48" width="35.22" height="1104" rx="17.6" fill="#3b8575"/>
        <rect x="35.22" y="48" width="35.22" height="1104" rx="17.6" fill="#ffffff"/>
        <rect x="70.44" y="48" width="35.22" height="1104" rx="17.6" fill="#b3154a"/>
      </pattern>
      <pattern id="tabs-left" x="0" y="97" width="849" height="108" patternUnits="userSpaceOnUse">
        <rect x="58" y="0" width="80" height="36" rx="18" fill="#b3154a"/>
        <rect x="58" y="36" width="80" height="36" rx="18" fill="#ffffff"/>
        <rect x="58" y="72" width="80" height="36" rx="18" fill="#3b8575"/>
      </pattern>
      <pattern id="tabs-right" x="0" y="97" width="849" height="108" patternUnits="userSpaceOnUse">
        <rect x="712" y="0" width="80" height="36" rx="18" fill="#3b8575"/>
        <rect x="712" y="36" width="80" height="36" rx="18" fill="#ffffff"/>
        <rect x="712" y="72" width="80" height="36" rx="18" fill="#b3154a"/>
      </pattern>
    </defs>
    <rect class="tabs-top" x="107" y="48" width="636" height="80" fill="url(#tabs-row)"/>
    <rect class="tabs-bottom" x="107" y="1072" width="636" height="80" fill="url(#tabs-row)"/>
    <rect class="tabs-left" x="58" y="97" width="80" height="1006" fill="url(#tabs-left)"/>
    <rect class="tabs-right" x="712" y="97" width="80" height="1006" fill="url(#tabs-right)"/>
  </svg>

  <div class="menu-panel"></div>

  <p class="crest-name">Casa Morellina</p>

  <section class="dish dish--francaise">
    <h2 class="dish-name">Francaise</h2>
    <p class="dish-desc">
      <span class="line">Egg battered finished in a lemon chardonnay butter sauce, served over</span>
      <span class="line line--last">penne pasta</span>
    </p>
    <p class="dish-price">Chicken 18.95</p>
    <p class="dish-price">Veal 21.95</p>
  </section>

  <section class="dish dish--saltimbocca">
    <h2 class="dish-name">Saltimbocca</h2>
    <p class="dish-desc">
      <span class="line">Prosciutto topped with Ricotta and Mozzarella cheese, in a Marsala demi-</span>
      <span class="line line--last">glaze sauce, served over sautéed spinach and penne pasta</span>
    </p>
    <p class="dish-price">Chicken 20.95</p>
    <p class="dish-price">Veal 22.95</p>
  </section>

  <section class="dish dish--margarita">
    <h2 class="dish-name">Margarita</h2>
    <p class="dish-desc">
      <span class="line">Sautéed with Sundried Tomatoes, roasted Garlic in a creamy balsamic re-</span>
      <span class="line">duction sauce, topped with fresh Mozzarella cheese, served over penne</span>
      <span class="line line--last">pasta</span>
    </p>
  </section>

  <section class="dish dish--sorrento">
    <h2 class="dish-name">Sorrento</h2>
    <p class="dish-desc">
      <span class="line">Prosciutto topped with Eggplant, Roasted Red Peppers, Mushrooms, Ri-</span>
      <span class="line">cotta and fresh Mozzarella cheese in a creamy Tomato sauce served over</span>
      <span class="line line--last">penne pasta</span>
    </p>
    <p class="dish-price">Chicken 20.95</p>
    <p class="dish-price">Veal 22.95</p>
  </section>

  <svg class="dish-photo" width="849" height="1200" viewBox="0 0 849 1200">
    <defs>
      <radialGradient id="plate-tones" cx="0.5" cy="0.6" r="0.6">
        <stop offset="0" stop-color="#6b3a22"/>
        <stop offset="0.35" stop-color="#c9b48a"/>
        <stop offset="0.7" stop-color="#e9e6e0"/>
        <stop offset="1" stop-color="#3a2c22"/>
      </radialGradient>
    </defs>
    <ellipse class="photo-ring" cx="425" cy="903" rx="239" ry="155" fill="var(--crimson)"/>
    <ellipse class="photo-fill" cx="408" cy="880" rx="218" ry="134" fill="url(#plate-tones)"
             role="img" aria-label="Photo of plated lamb chops with brown sauce, mashed potatoes and asparagus"/>
  </svg>
</div>
</body>
</html>
```